Corvane Card

The logo is the Spanish flag colors I want a vibrant eye catching design with the yellow / red colors over either Navy or white background or black even ,
Would like a 2D feel to the logo with another lighter color logo under it look ,

Contact Information for Business Card

Corvane Flooring
Teodor Vashkin
Main Number
Cell Number
Fax Number

Website on the side of the card somewhere

Font styles to use
Sans Serif

Colors
ec1f27
ffc214

Requirements
Must have
• 2 logos feel one is bolder and the other one underneath very light

```html
<!DOCTYPE html>
<html lang="en">
<head>
<meta charset="utf-8">
<title>Corvane Flooring — Business Card</title>
<link rel="stylesheet" href="https://fonts.googleapis.com/css2?family=Syncopate:wght@700&family=Arimo:wght@400&display=swap">
<style>
  :root {
    --brand-red: #ec1f27;
    --brand-yellow: #ffc214;
    --card-ink: #252527;
    --card-ink-soft: #2c2c2f;
    --page-bg: #0c0c0d;
    --text-light: #f2f2f2;
    --rule: #58585c;
    --watermark: rgba(255, 255, 255, 0.08);
  }
  * { box-sizing: border-box; margin: 0; padding: 0; }
  html, body {
    width: 1200px; height: 820px; overflow: hidden;
    background: var(--page-bg);
  }
  .stage { position: relative; width: 1200px; height: 820px; }

  .card {
    position: absolute; top: 255px;
    width: 540px; height: 310px;
    background: linear-gradient(160deg, var(--card-ink-soft), var(--card-ink));
    border-left: 2px solid var(--brand-yellow);
    border-bottom: 2px solid var(--brand-yellow);
    overflow: hidden;
  }
  .card--front { left: 40px; }
  .card--back { left: 620px; }

  /* Bold wordmark */
  .wordmark {
    position: absolute;
    display: flex; align-items: center; gap: 12px;
    white-space: nowrap;
  }
  .wordmark__dot {
    width: 18px; height: 18px; border-radius: 4px;
    background: var(--brand-yellow);
  }
  .wordmark__name {
    font-family: "Syncopate", sans-serif;
    font-weight: 700;
    font-size: 18px; letter-spacing: 1px;
    color: var(--brand-red);
    text-transform: uppercase;
    line-height: 1.3;
  }
  .card--front .wordmark { top: 60px; right: 36px; }
  .card--back .wordmark { top: 228px; right: 34px; }
  .card--back .wordmark__name { font-size: 17px; }

  /* Light wordmark, set large and faint on the back */
  .wordmark-light {
    position: absolute; left: 28px; top: 30px;
    font-family: "Syncopate", sans-serif;
    font-weight: 700;
    font-size: 50px; line-height: 1.15;
    letter-spacing: 1px;
    color: var(--watermark);
    text-transform: uppercase;
    white-space: nowrap;
  }

  .divider { position: absolute; height: 1px; background: var(--rule); }
  .divider--top { left: 160px; right: 36px; top: 118px; }
  .divider--name { left: 30px; width: 250px; top: 212px; }

  .person-name {
    position: absolute; left: 30px; top: 180px;
    font-family: "Syncopate", sans-serif;
    font-weight: 700;
    font-size: 18px; letter-spacing: 0.5px;
    text-transform: uppercase;
    white-space: nowrap;
  }
  .person-name__first { color: var(--brand-red); }
  .person-name__last { color: var(--brand-yellow); }

  .contact-list {
    position: absolute; list-style: none;
    font-family: "Arimo", sans-serif;
    font-size: 15px; color: var(--text-light);
    white-space: nowrap;
  }
  .contact-list li {
    display: flex; align-items: center; gap: 10px;
    height: 24px;
  }
  .contact-list svg { width: 14px; height: 14px; fill: var(--brand-red); flex: none; }
  .contact-list--phones { left: 30px; top: 226px; }
  .contact-list--online { right: 30px; top: 240px; }
  .contact-list--online li { justify-content: flex-end; }
  .accent-red { color: var(--brand-red); }
</style>
</head>
<body>
<main class="stage">

  <section class="card card--front" aria-label="Business card front">
    <div class="wordmark">
      <span class="wordmark__dot"></span>
      <span class="wordmark__name">Corvane Flooring</span>
    </div>
    <div class="divider divider--top"></div>

    <h1 class="person-name">
      <span class="person-name__first">Teodor</span>
      <span class="person-name__last">Vashkin</span>
    </h1>
    <div class="divider divider--name"></div>

    <ul class="contact-list contact-list--phones">
      <li>
        <svg viewBox="0 0 16 16"><path d="M1 5c0-2 3-3 7-3s7 1 7 3v2h-4V5H5v2H1z M3 8h10l1 6H2z"/></svg>
        402 555 0161
      </li>
      <li>
        <svg viewBox="0 0 16 16"><path d="M4 1h8v14H4z M5.5 2.5v9h5v-9z" fill-rule="evenodd"/></svg>
        402 555 0174
      </li>
      <li>
        <svg viewBox="0 0 16 16"><path d="M4 1h8v4H4z M1 6h14v6h-3v3H4v-3H1z M5 10v4h6v-4z" fill-rule="evenodd"/></svg>
        402 555 0189
      </li>
    </ul>

    <ul class="contact-list contact-list--online">
      <li>hello@corvanefloors.com
        <svg viewBox="0 0 16 16"><path d="M1 3h14v10H1z"/><path d="M1 3l7 6 7-6" fill="none" stroke="#252527" stroke-width="1.4"/></svg>
      </li>
      <li><span>www.<span class="accent-red">corvanefloors</span>.com</span>
        <svg viewBox="0 0 16 16"><circle cx="8" cy="8" r="7"/></svg>
      </li>
    </ul>
  </section>

  <section class="card card--back" aria-label="Business card back">
    <div class="wordmark-light" aria-hidden="true">Corvane<br>Flooring</div>
    <div class="wordmark">
      <span class="wordmark__name">Corvane Flooring</span>
    </div>
  </section>

</main>
</body>
</html>
```